Brightmill Data Works

Our company is about IT hardwares and IT solutions. IT hardware such as PC, RAMS, storage and servers. IT solutions such as project management, BA. We are also selling new technology too.

Target Market(s)

Consumer, Small to Medium Business, Corporate

Requirements
Must have
• The business card must have the following:
• Name:
• Title:
• Contact Number:
• Email address:
• Website:
• Color: Must match the logo color upgrade

```html
<!DOCTYPE html>
<html lang="en">
<head>
<meta charset="utf-8">
<title>Brightmill Data Works – Business Card</title>
<link rel="stylesheet" href="https://fonts.googleapis.com/css2?family=Roboto:wght@400;500;700&display=swap">
<style>
  :root {
    --backdrop: #2b2b2b;
    --orange-light: #dc9038;
    --orange-deep: #c8652a;
    --charcoal: #444444;
    --card-white: #ffffff;
    --pattern-gray: #4a4947;
    --pattern-warm: #56493d;
    --text-light: #ffffff;
  }
  * { margin: 0; padding: 0; box-sizing: border-box; }
  html, body {
    width: 1200px; height: 960px; overflow: hidden;
    background: var(--backdrop);
    font-family: "Roboto", Arial, sans-serif;
  }
  .canvas { position: relative; width: 1200px; height: 960px; }

  .card {
    position: absolute; width: 600px; height: 343px; overflow: hidden;
    box-shadow: 0 3px 8px rgba(0,0,0,.55);
  }
  .card-front {
    left: 322px; top: 108px;
    background: radial-gradient(ellipse at 30% 50%, var(--orange-light) 0%, var(--orange-deep) 75%);
  }
  .front-shape { position: absolute; inset: 0; }

  .contact-block { position: absolute; left: 25px; top: 110px; color: var(--text-light); }
  .holder-name { font-size: 20px; font-weight: 500; letter-spacing: .2px; line-height: 24px; }
  .holder-title { font-size: 15px; font-weight: 400; line-height: 20px; margin-bottom: 18px; }
  .contact-list { list-style: none; font-size: 14px; line-height: 19.5px; }
  .contact-list li { display: flex; align-items: center; gap: 7px; }
  .contact-list svg { width: 13px; height: 13px; fill: var(--text-light); flex: none; }

  .brand-front {
    position: absolute; left: 300px; width: 300px; top: 108px;
    display: flex; flex-direction: column; align-items: center;
  }
  .brand-square { width: 22px; height: 22px; background: var(--orange-deep); margin-bottom: 14px; }
  .brand-name {
    font-weight: 700; font-size: 30px; line-height: 34px; color: var(--charcoal);
    text-align: center; letter-spacing: .5px; text-transform: uppercase;
  }

  .card-back { left: 320px; top: 493px; height: 342px; }
  .back-pattern {
    position: absolute; inset: 0;
    background: radial-gradient(ellipse at 50% 50%, var(--pattern-warm) 0%, var(--pattern-gray) 80%);
  }
  .brand-back {
    position: absolute; inset: 0; display: flex; align-items: center; justify-content: center;
    font-weight: 700; font-size: 26px; color: var(--orange-light);
    letter-spacing: .5px; text-transform: uppercase;
  }
</style>
</head>
<body>
<main class="canvas">

  <section class="card card-front" aria-label="Business card front">
    <svg class="front-shape" viewBox="0 0 600 343" width="600" height="343" aria-hidden="true">
      <path d="M368 0 L240 140 Q222 171 240 202 L383 343 L600 343 L600 0 Z"
            fill="var(--charcoal)" stroke="var(--card-white)" stroke-width="2"/>
      <path d="M378 0 L250 140 Q234 171 250 202 L393 343 L600 343 L600 0 Z"
            fill="var(--card-white)"/>
    </svg>

    <div class="contact-block">
      <p class="holder-name">DANIEL REYES</p>
      <p class="holder-title">CEO/FOUNDER</p>
      <ul class="contact-list">
        <li>
          <svg viewBox="0 0 24 24"><path d="M6.6 10.8a15 15 0 0 0 6.6 6.6l2.2-2.2a1 1 0 0 1 1-.25 11.4 11.4 0 0 0 3.6.57 1 1 0 0 1 1 1V20a1 1 0 0 1-1 1A17 17 0 0 1 3 4a1 1 0 0 1 1-1h3.5a1 1 0 0 1 1 1c0 1.25.2 2.45.57 3.57a1 1 0 0 1-.25 1z"/></svg>
          555 014 2290
        </li>
        <li>
          <svg viewBox="0 0 24 24"><path d="M2 5h20v14H2z M2 5l10 8 10-8" fill="currentColor"/><path d="M2 6v13h20V6l-10 8z"/></svg>
          daniel@brightmill.com
        </li>
        <li>
          <svg viewBox="0 0 24 24"><circle cx="12" cy="12" r="10"/><path d="M12 2v20M2 12h20M12 2c4 4 4 16 0 20M12 2c-4 4-4 16 0 20" stroke="var(--orange-deep)" stroke-width="1.4" fill="none"/></svg>
          www.brightmill.com
        </li>
      </ul>
    </div>

    <div class="brand-front">
      <span class="brand-square" aria-hidden="true"></span>
      <p class="brand-name">Brightmill<br>Data Works</p>
    </div>
  </section>

  <section class="card card-back" aria-label="Business card back">
    <div class="back-pattern" role="img" aria-label="Faint repeating brand pattern on charcoal background"></div>
    <p class="brand-back">Brightmill Data Works</p>
  </section>

</main>
</body>
</html>
```